Business Card Design Project

I need a business card designed from scratch. I have an existing logo that I can upload in Illustrator for modification or redesign.

The Company is called Query Lanterns http://querylanterns.com.au and we provide Search Engine Optimization services to Australian businesses. The current logo signifies an increase in visitors, profits etc...

There are no restrictions as to the redesign - colours, style etc are all open to change.

Cards will be full colour and one sided printed at http://www.cardmoxel.com.au so check their requirements for file format and sizes etc.

I will expect all original files upon completion of project.

Target Market(s)

Any business with a web site looking to improve their search engine rankings

Industry/Entity Type

Business

Requirements
Must have
• I like modern, sleek designs. Clean, not fussy, uncluttered.

```html
<!DOCTYPE html>
<html lang="en">
<head>
<meta charset="utf-8">
<title>Query Lanterns – Business Card</title>
<link href="https://fonts.googleapis.com/css2?family=Open+Sans:wght@400;600;700;800&display=swap" rel="stylesheet">
<style>
  :root {
    --backdrop: #ece9e4;
    --card-white: #ffffff;
    --brand-blue: #1a6fb8;
    --deep-blue: #14589a;
    --brand-yellow: #f6c20f;
    --warm-yellow: #f5b414;
    --bright-yellow: #f5d600;
    --pale-yellow: #f3e34e;
    --ink-grey: #5a5a5a;
    --text-white: #ffffff;
  }
  * { margin: 0; padding: 0; box-sizing: border-box; }
  html, body { width: 1200px; height: 460px; overflow: hidden; }
  body {
    position: relative;
    background: var(--backdrop);
    font-family: "Open Sans", Arial, sans-serif;
  }
  .card {
    position: absolute;
    top: 74px;
    width: 545px;
    height: 311px;
    border-radius: 14px;
    overflow: hidden;
    box-shadow: 0 2px 6px rgba(0,0,0,0.18);
  }
  .card-front { left: 43px; background: var(--card-white); }
  .card-back {
    left: 614px;
    background: linear-gradient(90deg, var(--warm-yellow) 0%, var(--bright-yellow) 80%, var(--pale-yellow) 100%);
  }
  .wave { position: absolute; inset: 0; }
  .brand {
    position: absolute;
    left: 0; right: 0;
    display: flex;
    align-items: center;
    justify-content: center;
    gap: 12px;
  }
  .brand-dot {
    width: 22px; height: 22px;
    border-radius: 50%;
    background: var(--brand-yellow);
  }
  .card-back .brand-dot { background: var(--brand-blue); }
  .brand-name {
    font-weight: 800;
    font-size: 38px;
    color: var(--brand-blue);
    letter-spacing: -0.5px;
  }
  .card-front .brand { top: 80px; }
  .card-back .brand { top: 104px; }
  .holder {
    position: absolute;
    top: 160px;
    left: 0; right: 0;
    text-align: center;
    color: var(--deep-blue);
  }
  .holder-name { font-weight: 700; font-size: 17px; }
  .holder-title { font-size: 13px; margin-left: 4px; }
  .contacts {
    position: absolute;
    top: 248px;
    left: 28px;
    right: 14px;
    display: grid;
    grid-template-columns: 175px 130px 1fr;
    row-gap: 5px;
    color: var(--text-white);
    font-size: 13px;
    line-height: 14px;
  }
  .contact-item { display: flex; align-items: center; gap: 6px; white-space: nowrap; }
  .contact-item svg { width: 10px; height: 10px; flex: none; }
  .site-url {
    position: absolute;
    top: 212px;
    left: 0; right: 0;
    text-align: center;
    font-size: 12px;
    color: var(--ink-grey);
  }
</style>
</head>
<body>

<section class="card card-front" aria-label="Card front">
  <svg class="wave" viewBox="0 0 545 311" preserveAspectRatio="none" aria-hidden="true">
    <path d="M0 180 C120 186 250 214 545 192 L545 311 L0 311 Z" fill="var(--brand-yellow)"/>
    <path d="M0 208 C140 218 330 206 545 200 L545 311 L0 311 Z" fill="var(--brand-blue)"/>
  </svg>

  <div class="brand">
    <span class="brand-dot"></span>
    <span class="brand-name">Query Lanterns</span>
  </div>

  <p class="holder"><span class="holder-name">YOUR NAME</span><span class="holder-title">Title</span></p>

  <div class="contacts">
    <span class="contact-item">00Floor Street, City Name</span>
    <span class="contact-item">
      <svg viewBox="0 0 10 10"><path d="M2 1 L4 1 L4.6 3 L3.4 4 Q4.4 5.8 6 6.6 L7 5.4 L9 6 L9 8 Q8 9 6.5 8.6 Q2.2 7 1.2 3 Q1 1.8 2 1 Z" fill="none" stroke="var(--text-white)" stroke-width="1"/></svg>
      091 234 5678
    </span>
    <span class="contact-item">
      <svg viewBox="0 0 10 10"><rect x="0.5" y="2" width="9" height="6" fill="var(--text-white)"/></svg>
      enquiry@querylanterns.com.au
    </span>
    <span class="contact-item">State Name, Contry Name</span>
    <span class="contact-item">
      <svg viewBox="0 0 10 10"><rect x="2.5" y="0.5" width="5" height="9" rx="1" fill="var(--text-white)"/><rect x="3.5" y="1.8" width="3" height="5" fill="var(--brand-blue)"/></svg>
      091 234 5678
    </span>
    <span class="contact-item">
      <svg viewBox="0 0 10 10"><circle cx="5" cy="5" r="4.2" fill="var(--text-white)"/></svg>
      www.querylanterns.com.au
    </span>
  </div>
</section>

<section class="card card-back" aria-label="Card back">
  <div class="brand">
    <span class="brand-dot"></span>
    <span class="brand-name">Query Lanterns</span>
  </div>
  <p class="site-url">www.querylanterns.com.au</p>
</section>

</body>
</html>
```